The Copper Kite Website Redesign

I want a new design and website for www.thecopperkitebrookvale.com where part of the home page includes our daily specials from our POS Toast to be pulled from API. I have included photos and links to give you a better feel for the style of our restaurant.

Coding

Coded - Design and coding required

```html
<!DOCTYPE html>
<html lang="en">
<head>
<meta charset="utf-8">
<title>The Copper Kite – A Finer Diner</title>
<link href="https://fonts.googleapis.com/css2?family=Roboto:wght@400;500;700&family=Mountains+of+Christmas:wght@700&family=Yellowtail&display=swap" rel="stylesheet">
<style>
:root{
  --red:#f20a0a;
  --black:#000;
  --ink:#111;
  --dark:#2b2b2b;
  --white:#fff;
  --grey:#777;
}
*{box-sizing:border-box;margin:0;padding:0}
html,body{width:1200px;height:3734px;overflow:hidden;background:var(--black);font-family:Roboto,Arial,sans-serif;color:var(--white)}
.abs{position:absolute}
section,header,footer,.bar{position:relative;width:1200px;overflow:hidden}
.heading{font-family:"Mountains of Christmas",cursive;font-weight:700;color:var(--white);text-align:center;line-height:1;white-space:nowrap}
.script{font-family:Yellowtail,cursive;color:var(--red);text-align:center;white-space:nowrap}
.rule{display:inline-block;width:90px;height:10px;border-top:2px solid #fff;border-bottom:2px solid #fff;vertical-align:middle;margin:0 18px}
.btn{position:absolute;background:var(--red);color:#fff;border-radius:30px;font-weight:700;font-size:16px;display:flex;align-items:center;justify-content:center;gap:8px;text-transform:uppercase;white-space:nowrap}
.btn .dot{width:14px;height:14px;border-radius:50%;background:#fff;color:var(--red);font-size:10px;display:flex;align-items:center;justify-content:center}

.topbar{height:38px;background:#1a1a1a;font-size:13px;font-weight:500}
.topbar span{position:absolute;top:11px;white-space:nowrap}
.nav{height:85px;background:#111}
.brand{left:112px;top:24px;font-family:"Mountains of Christmas",cursive;font-weight:700;font-size:30px;color:#fff;white-space:nowrap}
.nav a{position:absolute;top:34px;font-size:15px;font-weight:500;color:#fff;text-decoration:none}
.nav a.active{color:var(--red)}

.hero{height:565px;background:radial-gradient(ellipse at 75% 45%,#7a4a24 0%,#4a2c16 40%,#2a1a10 80%)}
.hero-name{left:112px;top:130px;font-family:"Mountains of Christmas",cursive;font-weight:700;font-size:72px;color:#fff;white-space:nowrap}
.hero p{position:absolute;left:112px;top:268px;width:480px;font-size:16px;font-weight:500;line-height:27px}

.specials{height:457px;background:radial-gradient(ellipse at 50% 50%,#4a4a44 0%,#2e2c28 60%,#1a1918 100%)}
.specials p{position:absolute;left:190px;width:820px;top:202px;font-size:14px;line-height:24px;text-align:center}

.menu{height:782px;background:var(--black)}
.tab{position:absolute;top:183px;width:158px;height:50px;border-radius:25px;background:var(--dark);font-size:15px;display:flex;align-items:center;justify-content:center}
.tab.on{background:var(--red);font-weight:700}
.dish{position:absolute;border-radius:50%;border:6px solid #333}
.dish.big{border-color:var(--red)}
.dish-name{position:absolute;top:538px;width:200px;text-align:center;font-weight:700;font-size:16px}
.dots span{position:absolute;top:686px;width:12px;height:12px;border-radius:50%;border:1px solid #888}

.retail{height:616px;background:var(--red)}
.shot{position:absolute;top:181px;width:311px;height:228px}
.card{position:absolute;top:368px;width:280px;height:151px;background:#fff;text-align:center;color:#333}
.card h3{margin-top:22px;font-size:18px;color:var(--ink)}
.card p{margin-top:10px;font-size:13px;line-height:21px;color:var(--grey);padding:0 20px}
.card a{display:block;margin-top:10px;color:var(--red);font-size:13px;font-weight:700;text-decoration:underline}

.about{height:703px;background:var(--black)}
.about p{position:absolute;left:665px;width:425px;font-size:14px;line-height:22px;color:#ddd;text-align:justify}

.contact{height:434px;background:#000}
.contact h4{position:absolute;font-size:18px;font-weight:700}
.contact h4::after{content:"";position:absolute;left:0;top:30px;width:42px;height:3px;background:var(--red)}
.field{position:absolute;background:#fff;color:#999;font-size:11px;padding:10px}
.info{position:absolute;left:706px;display:flex;align-items:center;gap:20px;font-size:14px;line-height:22px}
.info i{width:40px;height:40px;border-radius:50%;background:var(--red);border:2px solid #fff;display:flex;align-items:center;justify-content:center;flex:none}

.bar{height:54px;background:#0d0d0d;font-size:13px}
.social{position:absolute;top:13px;width:28px;height:28px;border-radius:50%}
</style>
</head>
<body>

<div class="bar topbar">
  <span style="left:112px">◷ Opening Hours: Sat - Sun: 8 am - 3 pm</span>
  <span style="left:748px">✉ eat@thecopperkitebrookvale.com</span>
  <span style="left:970px">✆ (555) 014-2290</span>
</div>

<header class="nav">
  <div class="abs brand">The Copper Kite</div>
  <a class="active" style="left:436px">Home</a>
  <a style="left:507px">About Us</a>
  <a style="left:602px">Menu</a>
  <a style="left:671px">Retail</a>
  <a style="left:740px">Press</a>
  <a style="left:811px">Contact Us</a>
  <div class="btn" style="left:924px;top:20px;width:166px;height:45px;font-size:15px">Order Online</div>
</header>

<section class="hero" role="img" aria-label="Close-up of roasted breakfast potatoes with herbs">
  <div class="abs hero-name">The Copper Kite</div>
  <p>The doors of The Copper Kite: a finer diner were eagerly thrown open for the first time on December 28th 2004.</p>
  <div class="btn" style="left:112px;top:351px;width:224px;height:51px">Make a Booking <span class="dot">›</span></div>
</section>

<section class="specials" role="img" aria-label="Diner plate with eggs and potatoes on a checkered rim">
  <div class="abs script" style="left:0;width:1200px;top:88px;font-size:20px">Today Specials</div>
  <div class="abs heading" style="left:0;width:1200px;top:118px;font-size:46px"><span class="rule"></span>Our Daily Specials<span class="rule"></span></div>
  <p>Lorem ipsum dolor sit amet, consectetur adipiscing elit, sed do eiusmod tempor incididunt ut labore et dolore magna aliqua. Ut enim ad minim veniam, quis nostrud exercitation ullamco laboris nisi ut aliquip ex ea commodo consequat.</p>
  <div class="btn" style="left:460px;top:287px;width:280px;height:47px;font-size:15px">Check Out Our Specials <span class="dot">›</span></div>
</section>

<section class="menu">
  <div class="abs script" style="left:0;width:1200px;top:72px;font-size:20px">Menu</div>
  <div class="abs heading" style="left:0;width:1200px;top:105px;font-size:46px"><span class="rule"></span>Our Menu<span class="rule"></span></div>
  <div class="tab on" style="left:174px">All Things Eggs</div>
  <div class="tab" style="left:348px">Sweet Tooth</div>
  <div class="tab" style="left:522px">Green Things</div>
  <div class="tab" style="left:694px">On Bread</div>
  <div class="tab" style="left:868px">Other Stuff</div>

  <div class="dish" role="img" aria-label="Burger with egg and ham" style="left:119px;top:337px;width:181px;height:181px;background:radial-gradient(circle,#8a5a2a,#3d4a22)"></div>
  <div class="dish" role="img" aria-label="Fruit bowl with ice cream" style="left:314px;top:337px;width:181px;height:181px;background:radial-gradient(circle,#f2e8c8,#d89a20)"></div>
  <div class="dish" role="img" aria-label="Roasted potatoes" style="left:705px;top:337px;width:181px;height:181px;background:radial-gradient(circle,#8a5526,#3a2212)"></div>
  <div class="dish" role="img" aria-label="Huevos rancheros with peppers" style="left:901px;top:337px;width:181px;height:181px;background:radial-gradient(circle,#c8463a,#3e7a2a)"></div>
  <div class="dish big" role="img" aria-label="Waffles with fruit on a diner table" style="left:478px;top:305px;width:243px;height:243px;background:radial-gradient(circle,#c88a3a,#7a3a22)"></div>

  <div class="dish-name" style="left:109px">Garden Eggs &amp; Ham</div>
  <div class="dish-name" style="left:304px">Veggie Scramble</div>
  <div class="dish-name" style="left:695px">The Field Hand</div>
  <div class="dish-name" style="left:891px">Huevos Rancheros</div>
  <div class="abs" style="left:0;width:1200px;top:583px;text-align:center;font-weight:700;font-size:18px">The Harbor</div>
  <div class="abs" style="left:400px;width:400px;top:614px;text-align:center;font-size:14px;line-height:23px;color:#bbb">The Captain's Fave - a Scramble of Eggs with Fresh Mozzarella, Basil, Tomatoes, &amp; Green Olives <b style="color:var(--red);font-weight:500">$12.95</b></div>
  <div class="dots"><span style="left:578px"></span><span style="left:594px;background:var(--red);border-color:var(--red)"></span><span style="left:610px"></span></div>
</section>

<section class="retail">
  <div class="abs script" style="left:0;width:1200px;top:62px;font-size:20px;color:#fff">Shop</div>
  <div class="abs heading" style="left:0;width:1200px;top:100px;font-size:46px"><span class="rule"></span>Our Retail<span class="rule"></span></div>
  <div class="shot" role="img" aria-label="Three bottles of house hot sauce" style="left:112px;background:linear-gradient(135deg,#6a4a2a,#c83020)"></div>
  <div class="shot" role="img" aria-label="Gift card purchase at the counter" style="left:445px;background:linear-gradient(135deg,#e8e4de,#8a7a6a)"></div>
  <div class="shot" role="img" aria-label="Staff member wearing a diner t-shirt" style="left:778px;background:linear-gradient(135deg,#5a3020,#b87a4a)"></div>
  <div class="card" style="left:127px"><h3>Gust Sauces</h3><p>Can't get enough of The Copper Kite? Our three homemade hot sauces</p><a>READ MORE ›</a></div>
  <div class="card" style="left:460px"><h3>Gift Cards</h3><p>Gift Cards are available for purchase The Copper Kite in any denomination!</p><a>READ MORE ›</a></div>
  <div class="card" style="left:793px"><h3>T-Shirts</h3><p>T-Shirts are available in a variety of sizes and colors at The Copper Kite for</p><a>READ MORE ›</a></div>
</section>

<section class="about">
  <div class="abs" role="img" aria-label="Waffles with berries and syrup pitcher" style="left:150px;top:140px;width:400px;height:280px;border-radius:50%;transform:rotate(-35deg);background:radial-gradient(ellipse,#c98a3a,#6a2a1a)"></div>
  <div class="abs script" style="left:665px;top:130px;font-size:20px;text-align:left">Welcome To</div>
  <div class="abs heading" style="left:665px;top:162px;font-size:38px;text-align:left">About The Copper Kite<span class="rule" style="width:80px;margin-left:14px"></span></div>
  <p style="top:232px">The doors of The Copper Kite: a finer diner were eagerly thrown open for the first time on December 28th 2004. We welcomed our first customers and started our magnificent life as a business that continues on through today. Along with our beloved and inquisitive customers came the many questions of our origin.</p>
  <p style="top:366px">The most important of which we will address right here and now... "Why?" they asked "Why did you name your restaurant The Copper Kite?" We always swore we would make up some exciting folklore tale of the origin of our now-venerated name, but we never quite came up with a story glorious enough to do justice to the wonderment.</p>
  <div class="btn" style="left:665px;top:527px;width:176px;height:47px;font-size:15px">Read More <span class="dot">›</span></div>
</section>

<section class="contact">
  <h4 style="left:112px;top:66px">TALK TO US</h4>
  <div class="field" style="left:112px;top:134px;width:255px;height:33px">First Name</div>
  <div class="field" style="left:381px;top:134px;width:256px;height:33px">Last Name</div>
  <div class="field" style="left:112px;top:187px;width:255px;height:33px">Email Address</div>
  <div class="field" style="left:381px;top:187px;width:256px;height:33px">Phone Number</div>
  <div class="field" style="left:112px;top:240px;width:525px;height:70px">Message</div>
  <div class="btn" style="left:112px;top:346px;width:169px;height:38px;font-size:14px">Submit Now</div>

  <h4 style="left:706px;top:66px">CONTACT INFORMATION</h4>
  <div class="info" style="top:133px"><i><svg width="14" height="18" viewBox="0 0 14 18"><path d="M7 0a7 7 0 0 0-7 7c0 5 7 11 7 11s7-6 7-11a7 7 0 0 0-7-7z" fill="#fff"/><circle cx="7" cy="7" r="2.5" fill="#f20a0a"/></svg></i><span>1480 Linden Avenue Brookvale, Michigan<br>48000</span></div>
  <div class="info" style="top:197px"><i><svg width="16" height="16" viewBox="0 0 16 16"><path d="M3 1l3 3-2 2a10 10 0 0 0 6 6l2-2 3 3-2 2C6 15 1 10 1 3z" fill="#fff"/></svg></i><span>(555) 014-2290</span></div>
  <div class="info" style="top:251px"><i><svg width="16" height="12" viewBox="0 0 16 12"><rect width="16" height="12" rx="1" fill="#fff"/><path d="M0 1l8 6 8-6" stroke="#f20a0a" stroke-width="1.5" fill="none"/></svg></i><span>eat@thecopperkitebrookvale.com</span></div>
  <h4 style="left:706px;top:306px">OPENING HOURS</h4>
  <div class="abs" style="left:706px;top:356px;font-size:15px">Sat. - Sun: 8 a.m. - 3 p.m.</div>
</section>

<footer class="bar">
  <div class="abs" style="left:112px;top:19px">Copyright© 2025 <u>The Copper Kite</u> | All Rights Reserved</div>
  <div class="social" style="left:958px;background:var(--red)"></div>
  <div class="social" style="left:992px;background:#fff"></div>
  <div class="social" style="left:1025px;background:#fff"></div>
  <div class="social" style="left:1058px;background:#fff"></div>
  <div class="abs" style="left:1134px;top:20px;font-size:11px">C37</div>
</footer>

</body>
</html>
```